Business Card Design For A Renovation Contractor Company

We need a business card for a new company based in Singapore, our company name is "RB Tolvane". We are a renovation contractor that builds designs into reality. We build more of F&B restaurants, retail stores and commercial offices. We work very closely with designers. The final design should communicate to our client that we are a company that you can trust, that will plan and complete your project without giving you a headache. I like my client to remember my company as "RB". The beauty of SIMPLE is important.

Industry/Entity Type

Contractor

Requirements
Nice to have
• Black or Red base

```html
<!DOCTYPE html>
<html lang="en">
<head>
<meta charset="utf-8">
<title>RB Tolvane – Business Card</title>
<link rel="stylesheet" href="https://fonts.googleapis.com/css2?family=PT+Sans:wght@400;700&display=swap">
<style>
  :root {
    --ink: #111111;
    --paper: #ffffff;
    --accent: #e3202b;
    --stage: #ececec;
    --text-font: "PT Sans", Arial, sans-serif;
  }
  * { box-sizing: border-box; margin: 0; padding: 0; }
  html, body { width: 1200px; height: 720px; overflow: hidden; }
  body { background: var(--stage); font-family: var(--text-font); position: relative; }

  .card {
    position: absolute;
    width: 540px;
    height: 310px;
    overflow: hidden;
    box-shadow: 0 6px 18px rgba(0,0,0,0.18);
  }

  /* Front */
  .card--front { left: 50px; top: 50px; background: var(--paper); }
  .front-shape { position: absolute; inset: 0; width: 100%; height: 100%; }

  .brand {
    position: absolute;
    left: 30px;
    top: 112px;
    width: 250px;
  }
  .brand-mark {
    width: 46px; height: 46px;
    border-radius: 50%;
    background: var(--accent);
    margin: 0 0 10px 62px;
  }
  .brand-name {
    font-size: 40px;
    font-weight: 400;
    color: var(--ink);
    line-height: 1;
    letter-spacing: -0.5px;
  }
  .brand-tagline {
    margin-top: 5px;
    padding-top: 3px;
    border-top: 1.5px solid var(--ink);
    font-size: 15px;
    color: var(--accent);
    letter-spacing: 0.3px;
    white-space: nowrap;
  }

  .contact {
    position: absolute;
    right: 24px;
    top: 24px;
    color: var(--paper);
    text-align: right;
  }
  .contact-name { font-size: 18px; font-weight: 700; line-height: 1.1; }
  .contact-title { font-size: 12px; margin-bottom: 18px; }
  .contact-list { list-style: none; font-size: 13px; line-height: 1.45; }
  .contact-list li { display: flex; justify-content: flex-end; align-items: center; gap: 6px; }
  .contact-list svg { width: 11px; height: 11px; fill: var(--paper); }
  .contact-address { margin-top: 12px; font-size: 13px; line-height: 1.3; }

  /* Back */
  .card--back {
    left: 610px; top: 360px;
    background: var(--ink);
    color: var(--paper);
  }
  .back-mark {
    position: absolute;
    left: 50%; top: 36px;
    width: 160px; height: 160px;
    margin-left: -80px;
    border-radius: 50%;
    border: 20px solid var(--paper);
  }
  .back-name {
    position: absolute;
    left: 0; right: 0; top: 210px;
    text-align: center;
    font-size: 26px;
    font-weight: 400;
  }
  .back-web {
    position: absolute;
    left: 0; right: 0; bottom: 24px;
    text-align: center;
    font-size: 15px;
    letter-spacing: 4px;
  }
</style>
</head>
<body>

<section class="card card--front" aria-label="Business card front">
  <svg class="front-shape" viewBox="0 0 540 310" aria-hidden="true">
    <circle cx="545" cy="20" r="298" fill="var(--accent)"/>
    <circle cx="548" cy="18" r="284" fill="var(--paper)"/>
    <circle cx="550" cy="16" r="280" fill="var(--accent)"/>
    <circle cx="556" cy="10" r="270" fill="var(--ink)"/>
  </svg>

  <div class="brand">
    <div class="brand-mark"></div>
    <div class="brand-name">RB Tolvane</div>
    <div class="brand-tagline">your space, built right</div>
  </div>

  <div class="contact">
    <p class="contact-name">Your Name</p>
    <p class="contact-title">Title</p>
    <ul class="contact-list">
      <li>
        <svg viewBox="0 0 24 24"><path d="M6.6 10.8a15 15 0 0 0 6.6 6.6l2.2-2.2c.3-.3.7-.4 1-.2 1.1.4 2.3.6 3.6.6.6 0 1 .4 1 1V20c0 .6-.4 1-1 1A17 17 0 0 1 3 4c0-.6.4-1 1-1h3.5c.6 0 1 .4 1 1 0 1.3.2 2.5.6 3.6.1.3 0 .7-.2 1z"/></svg>
        123-456-0789
      </li>
      <li>
        <svg viewBox="0 0 24 24"><path d="M7 1h10a2 2 0 0 1 2 2v18a2 2 0 0 1-2 2H7a2 2 0 0 1-2-2V3a2 2 0 0 1 2-2zm0 3v14h10V4zm5 15.5a1.2 1.2 0 1 0 0 2.4 1.2 1.2 0 0 0 0-2.4z"/></svg>
        123-456-0789
      </li>
      <li>
        <svg viewBox="0 0 24 24"><path d="M2 5h20v14H2zm2 2v.5l8 5 8-5V7zm0 2.8V17h16V9.8l-8 5z"/></svg>
        info@rbtolvane.com
      </li>
      <li>
        <svg viewBox="0 0 24 24"><path d="M12 2a10 10 0 1 0 0 20 10 10 0 0 0 0-20zm0 2c.9 1.2 1.7 3 2 5h-4c.3-2 1.1-3.8 2-5zM4.3 13a8 8 0 0 1 0-2h3.7a17 17 0 0 0 0 2zm1 2h3a13 13 0 0 0 1.5 4A8 8 0 0 1 5.3 15zm3-6h-3a8 8 0 0 1 4.5-4A13 13 0 0 0 8.3 9zM12 20c-.9-1.2-1.7-3-2-5h4c-.3 2-1.1 3.8-2 5zm2.2-7H9.8a15 15 0 0 1 0-2h4.4a15 15 0 0 1 0 2zm.1 6a13 13 0 0 0 1.5-4h3a8 8 0 0 1-4.5 4zm1.7-6a17 17 0 0 0 0-2h3.7a8 8 0 0 1 0 2zm-.2-4a13 13 0 0 0-1.5-4 8 8 0 0 1 4.5 4z"/></svg>
        www.rbtolvane.com
      </li>
    </ul>
    <p class="contact-address">Street Name, City Name<br>State Zip Code</p>
  </div>
</section>

<section class="card card--back" aria-label="Business card back">
  <div class="back-mark"></div>
  <p class="back-name">RB Tolvane</p>
  <p class="back-web">www.rbtolvane.com</p>
</section>

</body>
</html>
```